We need a modern WIX website for Brightform Beam Services Australia (Laser/Industrial/Engineering)

We need a website for Wix (coded) for our laser restoration and industrial cleaning business.

It will need to be 4-6 pages.
Pages may include:
Home
About
Why Laser
Capabilities
There needs to be a contact / quote form

We do not want boring institutional design, so please do try to be a little creative (but not artsy, more engineering / laser etc). We hesitate with boxy wordpress looking templates, so please bring in strip backgrounds and sliders etc;

Our brand colours are blue and red, but a sharp modern site relative to the industry and work is important.

We envision the home page to take visitors on a informed journey of who, what, why, how, explaining the capability of laser science across contaminants, industries and surfaces.

We envision the home page to be strips:
- landing
- intro

-Why choose laser / What is laser cleaning
Minimum downtime, no surface damage, no environmental impact, no mess, no waste, complete restoration (we have an explainer video)

- Contaminants
Bacteria, Rust, Corrosion, Oxides, Grease, Oil, Paint, Stains, Mold, Soot / Carbon, Graffiti, Coatings, Dirt, Residue

- Surfaces
Metals, Engines/Parts/Components, Tools, Machinery, Bricks/Blockwork, Concrete, Paint, Stone, Wood, Aluminium

- Industries
Medical/Sterile, Hospitality, Bio Hazardous, Construction, Infrastructure, Property, Industrial, Engineer, Automotive, Marine, Heritage, Non Destructive Testing,

----
Here is some info on the company below:

"Background Information - Brightform Beam Services Australia (BBSA) is a leading provider of advanced laser restoration services for the residential, commercial, medical, hazardous and industrial sectors, offering waste free, chemical free and damage free complete restoration of metals, concrete, wood, stone and heritage, hygiene and hazard surfaces, with complete removal of coatings, bacteria, paint, rust, graffiti, mold and fire ash (soot), and preparation and treating for welding and bonding.
Servicing Melbourne and Victoria, with additional services available Australia wide, BBSA offers a 24/7 call-out service to your site.
With no downtime to your operations, we offer a timely resolution to your cleaning and maintenance needs."

We have attached some inspiration of websites we like the flow/feel of, but feel free to put your best designs forward.

You are welcome to use dummy headers and text at this stage, as design and feel is most important, and we can add text later.

```html
<!DOCTYPE html>
<html lang="en">
<head>
<meta charset="utf-8">
<title>Brightform Beam Services Australia</title>
<link href="https://fonts.googleapis.com/css2?family=Michroma&family=Open+Sans:wght@400;600&display=swap" rel="stylesheet">
<style>
:root{
  --red:#e91c24;
  --blue:#1566b8;
  --black:#050505;
  --panel:#141414;
  --card:#1b1b1b;
  --white:#ffffff;
  --muted:#cfcfcf;
  --display:'Michroma',sans-serif;
  --body:'Open Sans',sans-serif;
}
*{margin:0;padding:0;box-sizing:border-box}
html,body{width:1200px;height:4535px;overflow:hidden;background:var(--black)}
body{font-family:var(--body);color:var(--white)}
.page{position:relative;width:1200px;height:4535px;overflow:hidden;background:var(--black)}
.abs{position:absolute}
.display{font-family:var(--display);text-transform:uppercase;letter-spacing:.02em}
.btn{position:absolute;display:flex;align-items:center;justify-content:center;border-radius:26px;font-family:var(--display);text-transform:uppercase;color:var(--white);font-size:14px}
.btn-red{background:var(--red)}
.btn-blue{background:var(--blue)}
.blob{position:absolute}
.vertical-word{position:absolute;font-family:var(--display);text-transform:uppercase;color:transparent;-webkit-text-stroke:1.5px #5a5a5a;white-space:nowrap;transform:rotate(-90deg);transform-origin:left top;line-height:1}
.arrow{position:absolute;width:20px;height:20px;border-radius:50%;display:flex;align-items:center;justify-content:center}
.arrow svg{width:10px;height:10px}

/* header & hero */
.hero{position:absolute;left:0;top:0;width:1200px;height:700px}
.hero-photo{position:absolute;inset:0;background:radial-gradient(ellipse at 70% 55%,#7a3a12 0%,#3a2416 30%,#1a1b1e 65%,#101113 100%)}
.nav-bar{position:absolute;left:0;top:0;width:1200px;height:88px;background:rgba(20,20,20,.55)}
.brand{position:absolute;left:109px;top:24px;font-family:var(--display);font-size:34px;color:var(--white);letter-spacing:.04em}
.nav-link{position:absolute;top:36px;font-size:15px;color:var(--white)}
.nav-link.active{color:var(--red)}
.hero-kicker{left:111px;top:247px;font-size:22px;color:var(--red)}
.hero-title{left:109px;top:288px;font-size:46px;line-height:62px;color:var(--white)}

/* why laser */
.why{position:absolute;left:0;top:700px;width:1200px;height:599px;background:#0c0c0d}
.section-title{position:absolute;left:0;width:1200px;text-align:center;font-family:var(--display);text-transform:uppercase;font-size:34px}
.feature-active{position:absolute;left:303px;top:185px;width:186px;height:329px;background:#1a1a1a;border-radius:4px}
.feature{position:absolute;top:200px;width:220px;text-align:center}
.feature-ring{width:142px;height:142px;margin:0 auto;border:3px solid var(--white);border-radius:50%;display:flex;align-items:center;justify-content:center}
.feature-ring svg{width:70px;height:70px}
.feature-label{margin-top:30px;font-family:var(--display);font-size:15px;line-height:27px;text-transform:uppercase}

/* about */
.about{position:absolute;left:0;top:1299px;width:1200px;height:619px;background:var(--panel)}
.about-photo{position:absolute;left:97px;top:74px;width:519px;height:466px}
.about-title{left:651px;top:132px;font-size:37px}
.about-copy{position:absolute;left:653px;top:196px;width:452px;font-size:14.5px;line-height:30px;color:#e4e4e4}

/* contaminants */
.contam{position:absolute;left:0;top:1918px;width:1200px;height:680px;background:var(--black)}
.ghost-word{position:absolute;left:0;top:87px;width:1200px;text-align:center;font-family:var(--display);font-size:56px;color:transparent;-webkit-text-stroke:1px #5a5a5a;text-transform:uppercase}
.contam-card{position:absolute;top:206px;width:234px;height:326px;display:flex;align-items:center;justify-content:center;font-family:var(--display);font-size:22px;text-transform:uppercase;color:var(--white)}

/* surfaces */
.surfaces{position:absolute;left:0;top:2598px;width:1200px;height:640px;background:var(--black)}
.surface-card{position:absolute;width:461px;height:175px;background:var(--panel);border-radius:6px}
.surface-icon{position:absolute;left:12px;top:14px;width:62px;height:62px;border-radius:50%;background:#2a2a2a;display:flex;align-items:center;justify-content:center}
.surface-icon svg{width:32px;height:32px}
.surface-name{position:absolute;left:89px;top:24px;font-family:var(--display);font-size:19px;text-transform:uppercase}
.surface-copy{position:absolute;left:91px;top:58px;width:350px;font-size:14px;line-height:26px;color:#e4e4e4}
.surface-link{position:absolute;left:91px;top:136px;font-family:var(--display);font-size:13px;color:var(--blue);text-transform:uppercase}

/* industries */
.industries{position:absolute;left:0;top:3238px;width:1200px;height:748px;background:var(--black)}
.industry-card{position:absolute;top:136px;width:371px;height:417px;border-radius:4px;overflow:hidden}
.industry-photo{position:absolute;inset:0}
.industry-label{position:absolute;left:32px;bottom:32px;font-family:var(--display);font-size:25px;text-transform:uppercase}
.industry-go{position:absolute;right:32px;bottom:32px;width:22px;height:22px;border-radius:50%;background:var(--red);display:flex;align-items:center;justify-content:center}

/* newsletter & footer */
.lower{position:absolute;left:0;top:3986px;width:1200px;height:549px;background:#0f0f10}
.signup-field{position:absolute;left:199px;top:175px;width:602px;height:52px;border:1px solid #cfcfcf;background:#0f0f10;font-size:14px;padding:15px 24px;color:#dcdcdc}
.signup-btn{position:absolute;left:801px;top:175px;width:225px;height:52px;background:var(--red);display:flex;align-items:center;justify-content:center;font-family:var(--display);font-size:15px}
.footer-brand{position:absolute;left:126px;top:303px;font-family:var(--display);font-size:38px;letter-spacing:.04em}
.contact-icon{position:absolute;top:296px;width:42px;height:42px;border-radius:50%;background:#2b2b2b;display:flex;align-items:center;justify-content:center}
.contact-icon svg{width:18px;height:18px}
.contact-head{position:absolute;top:346px;font-family:var(--display);font-size:14px}
.contact-text{position:absolute;font-size:14px;line-height:26px;color:#e4e4e4}
.footer-rule{position:absolute;left:111px;top:446px;width:978px;height:1px;background:#3a3a3a}
.copyright{position:absolute;left:0;top:480px;width:1200px;text-align:center;font-size:14px;color:#e4e4e4}
</style>
</head>
<body>
<div class="page">

  <!-- Hero -->
  <section class="hero">
    <div class="hero-photo" role="img" aria-label="Welder grinding metal with a shower of orange sparks in a dark workshop"></div>
    <div class="nav-bar"></div>
    <div class="brand">BBSA</div>
    <a class="nav-link active" style="left:528px">Home</a>
    <a class="nav-link" style="left:612px">About</a>
    <a class="nav-link" style="left:697px">Why Laser</a>
    <a class="nav-link" style="left:811px">Capabilities</a>
    <div class="btn btn-red" style="left:947px;top:18px;width:158px;height:49px">Quote Form</div>
    <svg class="blob" style="left:1050px;top:0" width="150" height="400" viewBox="0 0 150 400"><path d="M150 0 L150 400 C90 410 40 380 30 350 C10 300 60 150 110 40 C120 15 135 0 150 0Z" fill="var(--red)"/></svg>
    <div class="abs display hero-kicker">Welcome to</div>
    <h1 class="abs display hero-title">Brightform Beam Services<br>Australia</h1>
    <div class="btn btn-red" style="left:111px;top:431px;width:197px;height:49px">Get Started</div>
  </section>

  <!-- Why laser -->
  <section class="why">
    <div class="section-title" style="top:88px">Why Choose Laser</div>
    <div class="vertical-word" style="left:1118px;top:580px;font-size:80px">Why Choose</div>
    <div class="feature-active"></div>
    <div class="arrow" style="left:74px;top:272px;background:var(--red)"><svg viewBox="0 0 10 10"><path d="M6.5 1.5 3 5l3.5 3.5" fill="none" stroke="#fff" stroke-width="1.6"/></svg></div>
    <div class="arrow" style="left:1090px;top:272px;background:var(--blue)"><svg viewBox="0 0 10 10"><path d="M3.5 1.5 7 5 3.5 8.5" fill="none" stroke="#fff" stroke-width="1.6"/></svg></div>

    <div class="feature" style="left:85px">
      <div class="feature-ring"><svg viewBox="0 0 70 70" fill="none" stroke="#fff" stroke-width="2.5"><path d="M22 20a22 22 0 1 1-4 27"/><path d="M16 14v9h9"/><path d="M35 24v12l8 6"/></svg></div>
      <div class="feature-label">Minimum<br>Downtime</div>
    </div>
    <div class="feature" style="left:286px">
      <div class="feature-ring"><svg viewBox="0 0 70 70" fill="none" stroke="#fff" stroke-width="2.5"><path d="M10 52 26 30l8 10 6-6 20 18Z"/><path d="M44 10v10M39 15h10M54 22v6M51 25h6"/></svg></div>
      <div class="feature-label" style="margin-top:30px">No Surface<br>Damage</div>
    </div>
    <div class="feature" style="left:518px">
      <div class="feature-ring"><svg viewBox="0 0 70 70" fill="none" stroke="#fff" stroke-width="2.5"><circle cx="35" cy="35" r="26"/><path d="M29 18h12v6l4 6v22H25V30l4-6Z"/><path d="M16 16l38 38"/></svg></div>
      <div class="feature-label">No Environmental<br>Impact</div>
    </div>
    <div class="feature" style="left:719px">
      <div class="feature-ring"><svg viewBox="0 0 70 70" fill="none" stroke="#fff" stroke-width="2.5"><circle cx="35" cy="35" r="26"/><path d="M24 24l22 22M46 24 24 46"/></svg></div>
      <div class="feature-label" style="margin-top:34px">No Mess</div>
    </div>
    <div class="feature" style="left:898px">
      <div class="feature-ring"><svg viewBox="0 0 70 70" fill="none" stroke="#fff" stroke-width="2.5"><circle cx="35" cy="35" r="26"/><path d="M23 24h24M30 24v-4h10v4M26 24l2 24h14l2-24"/><path d="M16 16l38 38"/></svg></div>
      <div class="feature-label" style="margin-top:34px">No Waste</div>
    </div>
    <div class="btn btn-blue" style="left:336px;top:434px;width:127px;height:38px;font-size:11px">Learn More</div>
  </section>

  <!-- About -->
  <section class="about">
    <div class="vertical-word" style="left:22px;top:566px;font-size:72px">About Us</div>
    <svg class="about-photo" viewBox="0 0 519 466" role="img" aria-label="Welder in a protective mask cutting metal, framed in a rounded triangle">
      <defs><linearGradient id="aboutTone" x1="0" y1="0" x2="1" y2="1"><stop offset="0" stop-color="#3b4a66"/><stop offset=".55" stop-color="#7a3d1a"/><stop offset="1" stop-color="#1d2436"/></linearGradient></defs>
      <path d="M230 20 C250 -5 280 -5 300 20 L505 400 C520 440 500 466 460 466 L60 466 C20 466 0 440 14 400Z" fill="url(#aboutTone)"/>
    </svg>
    <div class="abs display about-title">About Us</div>
    <p class="about-copy">Brightform Beam Services Australia (BBSA) is a leading provider of advanced laser restoration services for the residential, commercial, medical, hazardous and industrial sectors, offering waste free, chemical free and damage free complete restoration of metals, concrete, wood, stone and heritage, hygiene and hazard surfaces, with complete removal of coatings, bacteria, paint, rust, graffiti, mold and fire ash (soot), and preparation and treating for welding and bonding.</p>
    <div class="btn btn-blue" style="left:651px;top:456px;width:159px;height:40px;font-size:12px">Learn More</div>
    <svg class="blob" style="left:1050px;top:290px" width="150" height="340" viewBox="0 0 150 340"><path d="M150 0 L150 340 L10 340 C0 320 20 260 60 180 C100 100 130 20 150 0Z" fill="var(--red)"/></svg>
  </section>

  <!-- Contaminants -->
  <section class="contam">
    <div class="ghost-word">Contaminants</div>
    <div class="section-title" style="top:112px;font-size:33px">We Clean Contaminants Like</div>
    <div class="contam-card" style="left:93px;background:radial-gradient(circle at 50% 50%,#5f7a3a,#2a3a2a 60%,#111 100%)" role="img" aria-label="Microscopic bacteria in a petri dish"><span>Bacteria</span></div>
    <div class="contam-card" style="left:352px;background:linear-gradient(160deg,#a0581c,#7b3f15 60%,#9a5420)" role="img" aria-label="Rusted metal sheet"><span>Rust</span></div>
    <div class="contam-card" style="left:609px;background:linear-gradient(160deg,#8a6a3a,#3a3e48 55%,#a04a2a)" role="img" aria-label="Engineers inspecting corroded equipment"><span>Corrosion</span></div>
    <div class="contam-card" style="left:866px;background:linear-gradient(160deg,#8c8c8c,#2e2e2e 50%,#b8b8b8)" role="img" aria-label="Crinkled oxidised metal foil"><span>Oxides</span></div>
    <div class="arrow" style="left:42px;top:362px;background:var(--red)"><svg viewBox="0 0 10 10"><path d="M6.5 1.5 3 5l3.5 3.5" fill="none" stroke="#fff" stroke-width="1.6"/></svg></div>
    <div class="arrow" style="left:1130px;top:362px;background:var(--blue)"><svg viewBox="0 0 10 10"><path d="M3.5 1.5 7 5 3.5 8.5" fill="none" stroke="#fff" stroke-width="1.6"/></svg></div>
    <svg class="blob" style="left:0;top:370px" width="130" height="365" viewBox="0 0 130 365"><path d="M0 0 C30 60 90 200 120 290 C135 340 100 365 60 360 L0 360Z" fill="var(--red)"/></svg>
  </section>

  <!-- Surfaces -->
  <section class="surfaces">
    <div class="section-title" style="top:14px">Surfaces</div>
    <div class="vertical-word" style="left:1118px;top:520px;font-size:72px">Surfaces</div>

    <div class="surface-card" style="left:111px;top:107px">
      <div class="surface-icon"><svg viewBox="0 0 32 32" fill="none" stroke="#fff" stroke-width="1.8"><rect x="6" y="12" width="14" height="14"/><path d="M10 12V8h14v14h-4"/></svg></div>
      <div class="surface-name">Metals</div>
      <p class="surface-copy">Lorem ipsum dolor sit amet, consectetur adipiscing elit, sed do eiusmod tempor incididunt ut labore et dolore magna aliqua.</p>
      <div class="surface-link">Learn More</div>
    </div>
    <div class="surface-card" style="left:616px;top:107px">
      <div class="surface-icon"><svg viewBox="0 0 32 32" fill="none" stroke="#fff" stroke-width="1.8"><circle cx="16" cy="16" r="5"/><path d="M16 5v5M16 22v5M5 16h5M22 16h5M8 8l4 4M20 20l4 4M24 8l-4 4M12 20l-4 4"/></svg></div>
      <div class="surface-name">Engines</div>
      <p class="surface-copy">Have you been looking for a way to impress your friends with your amazing engineering skills? Looking to take your strategic skills to an adventurous</p>
      <div class="surface-link">Learn More</div>
    </div>
    <div class="surface-card" style="left:111px;top:313px">
      <div class="surface-icon"><svg viewBox="0 0 32 32" fill="none" stroke="#fff" stroke-width="1.8"><circle cx="12" cy="12" r="5"/><circle cx="22" cy="21" r="4"/><path d="M5 27h22"/></svg></div>
      <div class="surface-name">Machinery</div>
      <p class="surface-copy">Bring your family, friends, neighbors, or a stranger you just met, and join us for an action-packed 60 minutes that you won't forget!</p>
      <div class="surface-link">Learn More</div>
    </div>
    <div class="surface-card" style="left:616px;top:313px">
      <div class="surface-icon"><svg viewBox="0 0 32 32" fill="none" stroke="#fff" stroke-width="1.8"><rect x="5" y="7" width="22" height="18"/><path d="M5 13h22M5 19h22M14 7v6M20 13v6M12 19v6"/></svg></div>
      <div class="surface-name">Blockwork</div>
      <p class="surface-copy">Looking for an interactive experience for your entire group to enjoy together? Located only a short distance from downtown</p>
      <div class="surface-link">Learn More</div>
    </div>
    <div class="btn btn-red" style="left:502px;top:530px;width:197px;height:49px">View All</div>
  </section>

  <!-- Industries -->
  <section class="industries">
    <div class="vertical-word" style="left:16px;top:555px;font-size:72px">Industries</div>
    <div class="abs display" style="left:121px;top:45px;font-size:34px">Industries</div>
    <div class="btn btn-red" style="left:889px;top:30px;width:197px;height:51px">View All</div>

    <div class="industry-card" style="left:120px">
      <div class="industry-photo" role="img" aria-label="Medical staff in white coats working in a laboratory" style="background:linear-gradient(180deg,#d6dde0,#9aa6ad 55%,#3a3f44)"></div>
      <div class="industry-label">Medical</div>
      <div class="industry-go"><svg width="10" height="10" viewBox="0 0 10 10"><path d="M3.5 1.5 7 5 3.5 8.5" fill="none" stroke="#fff" stroke-width="1.6"/></svg></div>
    </div>
    <div class="industry-card" style="left:544px">
      <div class="industry-photo" role="img" aria-label="Workers in navy uniforms reviewing a tablet in a factory" style="background:linear-gradient(180deg,#7f8c99,#3c4a5c 55%,#1c2330)"></div>
      <div class="industry-label">Hospitality</div>
      <div class="industry-go"><svg width="10" height="10" viewBox="0 0 10 10"><path d="M3.5 1.5 7 5 3.5 8.5" fill="none" stroke="#fff" stroke-width="1.6"/></svg></div>
    </div>
    <div class="industry-card" style="left:968px;width:232px;border-radius:4px 0 0 4px">
      <div class="industry-photo" role="img" aria-label="Worker in an orange hazard suit inside a facility" style="background:linear-gradient(180deg,#9aa3aa,#6b4a32 55%,#24282c)"></div>
      <div class="industry-label">Bio Hazard</div>
    </div>
    <div class="arrow" style="left:109px;top:332px;background:var(--red)"><svg viewBox="0 0 10 10"><path d="M6.5 1.5 3 5l3.5 3.5" fill="none" stroke="#fff" stroke-width="1.6"/></svg></div>
    <div class="arrow" style="left:1124px;top:332px;background:var(--blue)"><svg viewBox="0 0 10 10"><path d="M3.5 1.5 7 5 3.5 8.5" fill="none" stroke="#fff" stroke-width="1.6"/></svg></div>
    <svg class="blob" style="left:1060px;top:562px" width="140" height="370" viewBox="0 0 140 370"><path d="M140 0 L140 370 C80 370 40 350 45 300 C50 240 90 120 120 40 C128 18 135 5 140 0Z" fill="var(--red)"/></svg>
  </section>

  <!-- Newsletter & footer -->
  <section class="lower">
    <div class="section-title" style="top:100px;font-size:33px">Sign Up Our Newsletter</div>
    <div class="signup-field">Enter Your Email</div>
    <div class="signup-btn">Subscribe</div>

    <div class="footer-brand">BBSA</div>

    <div class="contact-icon" style="left:430px"><svg viewBox="0 0 18 18" fill="#fff"><path d="M9 1a6 6 0 0 0-6 6c0 4.5 6 10 6 10s6-5.5 6-10a6 6 0 0 0-6-6Zm0 8.3A2.3 2.3 0 1 1 9 4.7a2.3 2.3 0 0 1 0 4.6Z"/></svg></div>
    <div class="contact-text" style="left:428px;top:340px;width:260px">12b Brightform Beam Services<br>Australia Lorem ipsum</div>

    <div class="contact-icon" style="left:738px"><svg viewBox="0 0 18 18" fill="#fff"><path d="M4 1.5 6.8 1l1.5 3.8-1.8 1.4a9 9 0 0 0 4.3 4.3l1.4-1.8 3.8 1.5-.5 2.8A2 2 0 0 1 13.5 15 12.5 12.5 0 0 1 1 2.5 2 2 0 0 1 4 1.5Z"/></svg></div>
    <div class="contact-head" style="left:743px">Phone</div>
    <div class="contact-text" style="left:745px;top:366px">+61 3 9000 0417</div>

    <div class="contact-icon" style="left:931px"><svg viewBox="0 0 18 18" fill="#fff"><path d="M2 4h14v1.2L9 10 2 5.2Zm0 2.8 7 4.8 7-4.8V14H2Z"/></svg></div>
    <div class="contact-head" style="left:937px">Email</div>
    <div class="contact-text" style="left:939px;top:366px">info@brightformbeam.example</div>

    <div class="footer-rule"></div>
    <div class="copyright">©Copyrights 2023 Brightform Beam Services Australia &nbsp;|&nbsp; All Rights Reserved</div>
  </section>

</div>
</body>
</html>
```